Bramwell Valley Hospital

We need a template for our hospital newsletter.

I am attaching what we did for December and also what we did for January. We like the January one better, but we need to keep the old style calendar.

I am also attaching the logo.

We need the document to be easily editable so that we can change the content month to month.

Industry/Entity Type

Hospital

```html
<!DOCTYPE html>
<html lang="en">
<head>
<meta charset="UTF-8">
<title>Bramwell Valley Hospital Newsletter</title>
<link href="https://fonts.googleapis.com/css2?family=Arimo:wght@400;700&family=Roboto+Condensed:wght@400;700&display=swap" rel="stylesheet">
<style>
  :root {
    --frame: #0b0b0b;
    --page: #ffffff;
    --red: #e3200f;
    --blue: #1f57c8;
    --heading: #1d62d6;
    --text: #333333;
    --sidebar: #e6e6e6;
    --footer: #545352;
    --white: #ffffff;
  }
  * { box-sizing: border-box; margin: 0; padding: 0; }
  html, body { width: 827px; height: 1200px; overflow: hidden; background: var(--frame); }
  body { position: relative; font-family: "Arimo", Arial, sans-serif; color: var(--text); }

  .masthead-photo {
    position: absolute; left: 28px; top: 0; width: 760px; height: 21px;
    background: linear-gradient(90deg, #8a6a55, #c9b9a8 40%, #7e5f4b 70%, #b7a08c);
  }
  .issue-bar {
    position: absolute; left: 28px; top: 21px; width: 760px; height: 28px;
    background: var(--red); color: var(--white);
    display: flex; align-items: center;
  }
  .issue-bar .issue { font-family: "Roboto Condensed", sans-serif; font-size: 15px; font-weight: 700; margin-left: 22px; width: 216px; }
  .issue-bar .site { font-size: 16px; font-weight: 700; letter-spacing: 0.2px; width: 318px; }
  .issue-bar .date { font-family: "Roboto Condensed", sans-serif; font-size: 12.5px; font-weight: 700; width: 102px; }
  .social {
    background: var(--white); height: 26px; width: 100px; border: 1px solid var(--red);
    display: flex; align-items: center; justify-content: center; gap: 6px;
  }
  .social span { width: 12px; height: 12px; border-radius: 2px; display: block; }

  .page {
    position: absolute; left: 28px; top: 49px; width: 760px; height: 1003px;
    background: var(--page);
  }

  .article { position: absolute; left: 16px; }
  .article h2 { font-size: 18.5px; font-weight: 400; color: var(--heading); margin-bottom: 4px; }
  .article p { font-size: 11.6px; line-height: 19.7px; text-align: justify; margin-bottom: 19.7px; }
  .article p.tight { margin-bottom: 0; }

  .pain { top: 15px; width: 512px; }
  .vascular { top: 412px; width: 512px; }
  .vascular .photo-row { display: flex; gap: 15px; margin-top: 8px; }
  .vascular .photo-row p { width: 296px; text-align: justify; margin-bottom: 0; }
  .facility-photo {
    flex: none; width: 212px; height: 105px; margin-top: -3px;
    background: linear-gradient(180deg, #0f1e4a 0%, #1b2f6b 45%, #8a6f5a 70%, #3d3a3a 100%);
  }
  .vascular .closing { width: 530px; margin-top: 27px; }

  .tips {
    position: absolute; left: 560px; top: 8px; width: 193px; height: 989px;
    background: var(--sidebar);
  }
  .tips h3 {
    background: var(--blue); color: var(--white); height: 34px;
    font-size: 16px; font-weight: 700; letter-spacing: 0.5px;
    display: flex; align-items: center; justify-content: center;
  }
  .tips p { font-size: 11.6px; line-height: 19.7px; text-align: center; padding: 10px 4px 0; }

  .services {
    position: absolute; left: 28px; top: 1052px; width: 760px; height: 109px;
    background: var(--footer); color: var(--white);
    font-family: "Roboto Condensed", sans-serif;
  }
  .services .label { position: absolute; left: 9px; top: 5px; font-size: 16.5px; }
  .services ul { position: absolute; top: 6px; list-style: none; font-size: 12.8px; line-height: 20.7px; }
  .services ul li::before { content: "•"; margin-right: 8px; }
  .services .col-a { left: 126px; }
  .services .col-b { left: 353px; }
  .emergency { position: absolute; left: 578px; top: 16px; width: 170px; text-align: center; font-weight: 700; }
  .emergency .call { font-size: 13px; line-height: 18px; }
  .emergency .phone { font-size: 21px; margin-top: 3px; }

  .copyright {
    position: absolute; left: 28px; top: 1161px; width: 760px; height: 30px;
    background: var(--blue); color: var(--white);
    font-family: "Roboto Condensed", sans-serif; font-size: 12px;
    display: flex; align-items: center; justify-content: center;
  }
</style>
</head>
<body>
  <div class="masthead-photo" role="img" aria-label="Hospital building exterior banner photo"></div>

  <header class="issue-bar">
    <div class="issue">ISSUE : 01</div>
    <div class="site">www.bramwellvalleyhospital.org</div>
    <div class="date">29 JULY 2014</div>
    <div class="social" aria-label="Social links">
      <span style="background:#1d6fb0"></span>
      <span style="background:#3aa7d8"></span>
      <span style="background:#3b5a9a"></span>
      <span style="background:#3fae3f"></span>
      <span style="background:#f29222"></span>
    </div>
  </header>

  <main class="page">
    <article class="article pain">
      <h2>Managing Your Pain</h2>
      <p>Pain can be difficult to describe, even by those that deal with its impact every day. One reason is that people feel pain differently. Also, the amount of pain people can tolerate is varied. It can be throbbing or dull, constant or come and go. Pain impacts how you feel physically and emotionally. It can lessen your ability to care for yourself, work or maintain relationships. If you are in pain, it is important you discuss it with your doctor. There are many treatments available to help manage your pain.</p>
      <p>Your doctor may recommend physical therapy, exercise or even avoiding certain activities or foods. Medication can play an important role. Your primary care doctor may instruct you to take over the counter or order prescription medications for you.</p>
      <p class="tight">Many types of pain can be treated with injections. Epidural steroid injections are used for some types of back, neck, arm or leg pain. These injections can improve pain and function for several months or even longer. They can be repeated to maintain the benefits. Injections are also used to treat trigger points. In these cases, there is commonly a trigger point that is tender and when pressed. Pain radiates out from the trigger point. These injections can be used to treat certain types of neck, back, shoulder, hip, arm or hand pain. If you are currently traveling to have injections for pain management talk to your doctor about having those services provided in Millbrook.</p>
    </article>

    <article class="article vascular">
      <h2>Vascular Disease Among Leading Causes of Death in US</h2>
      <p class="tight">Pain can be difficult to describe, even by those that deal with its impact every day. One reason is that people feel pain differently. Also, the amount of pain people can tolerate is varied. It can be throbbing or dull, constant or come and go. Pain impacts how you feel physically and emotionally. It can lessen your ability to care for yourself, work or maintain relationships. If you are in pain, it is important you discuss it with your doctor. There are many treatments available to help manage your pain.</p>
      <div class="photo-row">
        <p>Your doctor may recommend physical therapy, exercise or even avoiding certain activities or foods. Medication can play an important role. Your primary care doctor may instruct you to take over the counter or order prescription medications for you.</p>
        <div class="facility-photo" role="img" aria-label="Hospital entrance canopy lit at dusk"></div>
      </div>
      <div class="closing">
        <p class="tight">Your doctor may recommend physical therapy, exercise or even avoiding certain activities or foods. Medication can play an important role. Your primary care doctor may instruct you to take over the counter or order prescription medications for you.</p>
        <p class="tight">Many types of pain can be treated with injections. Epidural steroid injections are used for some types of back, neck, arm or leg pain. These injections can improve pain and function for several months or even longer. They can be repeated to maintain the benefits. Injections are also used to treat trigger points. In these cases, there is commonly a trigger point that is tender and when pressed. Pain radiates out from the trigger point. These injections can be used to treat certain types of neck, back, shoulder, hip, arm or hand pain. If you are currently traveling to have injections for pain management talk to your doctor about having those services provided in Millbrook.</p>
      </div>
    </article>

    <aside class="tips">
      <h3>TIPS CORNER</h3>
      <p>Nora Whitfield, CRNA, of Ashford Anesthetist Group provides Pain Management Injections in Millbrook at Bramwell Valley Hospital.</p>
    </aside>
  </main>

  <footer class="services">
    <div class="label">Other Services :</div>
    <ul class="col-a">
      <li>Cardiac Stress Test</li>
      <li>Ultrasound</li>
      <li>Lymphedema Therapy</li>
      <li>Skilled / Respite/Hospice</li>
      <li>Nuclear Medicine-Friday</li>
    </ul>
    <ul class="col-b">
      <li>24 Hour Emergency Room</li>
      <li>Vascular Studies-Mon. &amp;Wed.</li>
      <li>DOT Drug &amp; Alcohol Screening</li>
      <li>Chemo/Infusion Therapy</li>
      <li>Respiratory Therapy</li>
    </ul>
    <div class="emergency">
      <div class="call">CALL US FOR<br>IMERGENCY SERVICE<br>Specialty Clinic</div>
      <div class="phone">(555) 214- 7390</div>
    </div>
  </footer>

  <div class="copyright">Copyright © 2015 Bramwell Valley Hospital &nbsp; All Rights Reserved.</div>
</body>
</html>
```